Need a stunning home page for Car rental company

For a client, I need a slick and sumber home page design. It is a small, local car rental company, with a handful of cars available for rent.
Selling points: affordable lease, availability, always clean cars
The design should be:
- flat and modern
- no, or very few animations/sliders
- CTA: booking form for renting a car.
- 3 featured cars with images and facts (see website) with button to read more about the car.
- fullscreen background video can be an option
- main colour: #efba01
The site is under construction here:
http://solvikutleie.hammerlia.no/
Delivery requirements:
I need a layered & well organised PSD file delivered.

```html
<!DOCTYPE html>
<html lang="no">
<head>
<meta charset="utf-8">
<title>Solvik Utleie – Car Rental</title>
<link rel="stylesheet" href="https://fonts.googleapis.com/css2?family=Arimo:wght@400;700&family=Roboto+Condensed:wght@700&display=swap">
<style>
:root{
  --gold:#efba01;
  --gold-light:#f7cf3a;
  --orange:#e8a21a;
  --ink:#4a4a4a;
  --muted:#8c8c8c;
  --line:#e2e2e2;
  --panel:#f1f1f1;
  --dark:#232323;
  --form:#2e2e2e;
}
*{box-sizing:border-box;margin:0;padding:0}
html,body{width:686px;height:1200px;overflow:hidden;background:#fff}
body{position:relative;font-family:"Arimo",Arial,sans-serif;color:var(--ink)}
.abs{position:absolute}
.topline{left:0;top:0;width:686px;height:2px;background:var(--gold)}
.brand{left:75px;top:24px;font-size:19px;font-weight:700;letter-spacing:1px;color:var(--gold);display:flex;align-items:center;gap:7px}
.brand-dot{width:10px;height:10px;background:var(--ink);border-radius:50%}
.search{left:449px;top:25px;width:161px;height:21px;border:1px solid #ddd;border-radius:11px;font-size:6px;color:#aaa;padding:7px 11px;display:flex;justify-content:space-between}
.nav{left:0;top:70px;width:686px;height:32px;background:linear-gradient(#f7c93a,#e9b00a);display:flex;align-items:center;padding-left:92px;gap:0}
.nav a{color:#fff;font-size:8px;text-decoration:none;margin-right:28px}
.hero{left:0;top:102px;width:686px;height:271px;background:linear-gradient(100deg,#1d1e22 0%,#4a4240 35%,#b5683a 65%,#e9a256 80%,#3a2a24 100%)}
.hero-title{left:75px;top:134px;font-size:24px;font-weight:700;color:var(--orange)}
.hero-sub{left:75px;top:169px;width:340px;font-family:"Roboto Condensed",sans-serif;font-size:11.5px;line-height:16px;color:#fff}
.play{left:213px;top:229px}
.booking{left:431px;top:145px;width:174px;height:237px;background:var(--form);border:1px solid #888;box-shadow:0 6px 10px rgba(0,0,0,.25)}
.booking h3{font-weight:400;font-size:12.5px;color:#fff;padding:12px 0 8px 11px;border-bottom:1px solid #555}
.field{position:absolute;background:linear-gradient(#fff,#ddd);font-size:6.5px;color:#888;padding:6px 7px;height:20px}
.btn{position:absolute;background:linear-gradient(#ffd24a,var(--gold));color:#fff;font-weight:700;text-align:center;border-radius:3px}
.booking .btn{left:31px;top:199px;width:109px;height:25px;line-height:25px;font-size:10px;color:#b97d00}
.welcome{left:0;top:414px;width:686px;text-align:center;font-size:13px;font-weight:700}
.gold{color:var(--gold)}
.intro{left:98px;top:442px;width:490px;text-align:center;font-size:6px;line-height:14.5px;color:var(--muted)}
.offers{left:0;top:510px;width:686px;height:383px;background:var(--panel)}
.section-title{width:686px;left:0;text-align:center;font-size:13px;font-weight:700}
.car{top:557px;width:168px;height:319px;background:#f7f7f7;border:1px solid #ddd}
.car-photo{position:absolute;left:2px;top:1px;width:164px;height:108px}
.car h4{position:absolute;left:4px;top:120px;font-size:9px;color:var(--ink)}
.specs{position:absolute;left:4px;top:135px;width:158px;border-top:1px solid var(--line);font-size:6.5px;color:#999}
.specs div{display:flex;height:16px;align-items:center;padding-left:3px}
.specs span:first-child{width:101px}
.specs span:last-child{color:#555}
.specs .price{color:var(--gold);font-weight:700;font-size:7.5px;height:18px;border-bottom:1px solid var(--line);margin-bottom:3px}
.specs .price span:last-child{color:var(--gold)}
.specs .end{border-top:1px solid var(--line);height:0;margin-top:4px}
.car .btn{left:44px;top:287px;width:79px;height:20px;line-height:20px;font-size:7px;border-radius:10px}
.post-img{top:955px;width:100px;height:95px}
.post{top:956px;width:144px}
.post h5{font-size:7px;font-weight:400;color:var(--gold)}
.post h6{font-size:6.5px;font-weight:400;color:#333;margin-top:3px}
.post p{font-size:6px;line-height:12px;color:var(--muted);margin-top:5px}
.post .btn{position:static;display:block;margin-top:7px;width:52px;height:19px;line-height:19px;font-size:7px;border-radius:2px}
.divider{left:343px;top:955px;width:1px;height:95px;background:#ddd}
.footer{left:0;top:1091px;width:686px;height:109px;background:var(--dark)}
.socials{left:251px;top:1107px;display:flex;gap:5px}
.socials span{width:22px;height:22px;border-radius:50%;background:#fff}
.foot-rule{left:75px;top:1141px;width:536px;height:1px;background:#3a3a3a}
.foot-nav{left:0;top:1153px;width:686px;text-align:center;font-size:6px;color:#fff;word-spacing:2px}
.copy{left:0;top:1174px;width:686px;text-align:center;font-size:6px;color:#fff}
</style>
</head>
<body>
<div class="abs topline"></div>
<div class="abs brand"><span class="brand-dot"></span>SOLVIK UTLEIE</div>
<div class="abs search"><span>SEARCH</span>
  <svg width="7" height="7" viewBox="0 0 8 8"><circle cx="3.3" cy="3.3" r="2.4" fill="none" stroke="#999" stroke-width="1"/><path d="M5 5l2.5 2.5" stroke="#999" stroke-width="1"/></svg></div>
<nav class="abs nav">
  <a>HJEM</a><a>BILPARKEN VÅR</a><a>TJENESTER</a><a>KONTAKT OSS</a><a>BLOG</a><a>PAGE TEMPLATES</a><a>ABOUT US</a>
</nav>

<section class="abs hero" role="img" aria-label="Silver sports car driving on a road at sunset"></section>
<h1 class="abs hero-title">CAR RENTAL COMPANY</h1>
<p class="abs hero-sub">SED UT PERSPICIATIS UNDE OMNIS ISTE NATUS ERROR SIT VOLUPTATEM VITAEDICTA SUNT EXPLICABO.</p>
<svg class="abs play" width="34" height="34" viewBox="0 0 34 34"><circle cx="17" cy="17" r="15.5" fill="none" stroke="#fff" stroke-width="2"/><path d="M13 10l11 7-11 7z" fill="#fff"/></svg>

<form class="abs booking">
  <h3>A booking form to rent a car</h3>
  <div class="field" style="left:8px;top:44px;width:158px">Name :</div>
  <div class="field" style="left:8px;top:68px;width:158px">Email :</div>
  <div class="field" style="left:8px;top:92px;width:158px">Phone :</div>
  <div class="field" style="left:8px;top:116px;width:75px">Pick Up :</div>
  <div class="field" style="left:91px;top:116px;width:75px">Drop off :</div>
  <div class="field" style="left:8px;top:142px;width:158px;height:50px">Comments :</div>
  <div class="btn">BOOKING NOW</div>
</form>

<h2 class="abs welcome">VELKOMMEN TIL SOLVIK <span class="gold">UTLEIE – SOLVIKSTRAND</span></h2>
<p class="abs intro">Sed ut perspiciatis unde omnis iste natus error sit voluptatem accusantium doloremque laudantium, totam rem aperiam, eaque ipsa quae ab illo inventore veritatis et quasi architecto beatae vitae dicta sunt explicabo. Nemo enim ipsam voluptatem quia voluptas sit aspernatur aut odit aut fugit, sed quia consequuntur magniarch itvoluptatem voluptas sit aspernatur aut odit aut fugit, sed quia consequuntur magni dolores</p>

<section class="abs offers"></section>
<h2 class="abs section-title" style="top:529px">VÅRE <span class="gold">LEIETILBUD</span></h2>

<article class="abs car" style="left:75px">
  <div class="car-photo" role="img" aria-label="Silver saloon car parked by a glass building" style="background:linear-gradient(160deg,#5a5f66,#c9ccd0 55%,#8a8d91)"></div>
  <h4>VAREBILEN</h4>
  <div class="specs">
    <div class="price"><span>Pris per døgn</span><span>kr 600</span></div>
    <div><span>Biltype</span><span>Varebil</span></div>
    <div><span>Maks. pers</span><span>2</span></div>
    <div><span>Ant. dører</span><span>5</span></div>
    <div><span>Min. sjåføralder</span><span>21</span></div>
    <div><span>Girtype</span><span>Manuell</span></div>
    <div><span>Klimaanlegg?</span><span>Ja</span></div>
    <div><span>Ubegrenset km?</span><span>Nei</span></div>
    <div class="end"></div>
  </div>
  <div class="btn">RESERVÉR NÅ</div>
</article>
<article class="abs car" style="left:260px">
  <div class="car-photo" role="img" aria-label="Red sports coupe on a track" style="background:linear-gradient(180deg,#7a8a6e 0%,#c9c4b8 35%,#c2232a 60%,#4a4a4a 100%)"></div>
  <h4>VAREBILEN</h4>
  <div class="specs">
    <div class="price"><span>Pris per døgn</span><span>kr 600</span></div>
    <div><span>Biltype</span><span>Varebil</span></div>
    <div><span>Maks. pers</span><span>2</span></div>
    <div><span>Ant. dører</span><span>5</span></div>
    <div><span>Min. sjåføralder</span><span>21</span></div>
    <div><span>Girtype</span><span>Manuell</span></div>
    <div><span>Klimaanlegg?</span><span>Ja</span></div>
    <div><span>Ubegrenset km?</span><span>Nei</span></div>
    <div class="end"></div>
  </div>
  <div class="btn">RESERVÉR NÅ</div>
</article>
<article class="abs car" style="left:444px">
  <div class="car-photo" role="img" aria-label="Side of a silver car in motion at sunset" style="background:linear-gradient(120deg,#3f5d80,#e0a24a 40%,#9aa3ab 70%,#5d646b)"></div>
  <h4>VAREBILEN</h4>
  <div class="specs">
    <div class="price"><span>Pris per døgn</span><span>kr 600</span></div>
    <div><span>Biltype</span><span>Varebil</span></div>
    <div><span>Maks. pers</span><span>2</span></div>
    <div><span>Ant. dører</span><span>5</span></div>
    <div><span>Min. sjåføralder</span><span>21</span></div>
    <div><span>Girtype</span><span>Manuell</span></div>
    <div><span>Klimaanlegg?</span><span>Ja</span></div>
    <div><span>Ubegrenset km?</span><span>Nei</span></div>
    <div class="end"></div>
  </div>
  <div class="btn">RESERVÉR NÅ</div>
</article>

<h2 class="abs section-title" style="top:914px">
  <svg width="7" height="10" viewBox="0 0 7 10" style="margin-right:10px"><path d="M6 1L2 5l4 4" fill="none" stroke="#555" stroke-width="1.6"/></svg>LATEST <span class="gold">BLOG</span><svg width="7" height="10" viewBox="0 0 7 10" style="margin-left:10px"><path d="M1 1l4 4-4 4" fill="none" stroke="#555" stroke-width="1.6"/></svg>
</h2>

<div class="abs post-img" role="img" aria-label="Tropical coastline with palm tree" style="left:75px;background:linear-gradient(180deg,#6fa3d8,#3f7a4a 55%,#2a8fb0)"></div>
<div class="abs post" style="left:188px">
  <h5>LOREM IPSUM DOLORE</h5>
  <h6>Lorem ipsum dolor sit amet</h6>
  <p>Sed ut perspiciatis unde omnis iste natus error sit voluptatem accusantium doloremque laudantium, totam rem aperiam, eaque ipsa quae ab illo inve-neos qui ratione voluptatem sequi nesciunt</p>
  <span class="btn">MORE</span>
</div>
<div class="abs divider"></div>
<div class="abs post-img" role="img" aria-label="Beach with sun loungers under trees" style="left:356px;background:linear-gradient(180deg,#3e5a2c,#8aa3a6 50%,#d8cbb0)"></div>
<div class="abs post" style="left:469px">
  <h5>LOREM IPSUM DOLORE</h5>
  <h6>Lorem ipsum dolor sit amet</h6>
  <p>Sed ut perspiciatis unde omnis iste natus error sit voluptatem accusantium doloremque laudantium, totam rem aperiam, eaque ipsa quae ab illo inve-neos qui ratione voluptatem sequi nesciunt</p>
  <span class="btn">MORE</span>
</div>

<footer class="abs footer"></footer>
<div class="abs socials" aria-label="Social links"><span></span><span></span><span></span><span></span><span></span><span></span><span></span></div>
<div class="abs foot-rule"></div>
<div class="abs foot-nav">HJEM &nbsp;|&nbsp; BILPARKEN VÅR &nbsp;|&nbsp; TJENESTER &nbsp;|&nbsp; KONTAKT OSS &nbsp;|&nbsp; BLOG &nbsp;|&nbsp; PAGE TEMPLATES &nbsp;|&nbsp; ABOUT US</div>
<div class="abs copy">© Copy Rights 2014Solvikutleie.All Rights Reserved</div>
</body>
</html>
```